Pre-workout label and Super Greens label for Brightmoor Nutrition Supplements

I need a label design for Club Brightmoor's 2 supplements. The first is a Pre-workout. The Pre-workout label needs to be 11.25 x 2.5 inches. This label will go on a black container. The second is a Super-Green. The Super-Green label should be 11.25 x 4.25 inches and will go on a white container. We have been selling these for a few years but the current labels are a little meh. I'd like something trendier and bolder. Must keep the Club Brightmoor branding. All the nurtition data must appear . I attached the current designs so you can know the flavors, nutrtional data etc. Thank you!
Updates

I can upload the Club Brightmoor logo! If anyone can tell me how to do that.

```html
<!DOCTYPE html>
<html lang="en">
<head>
<meta charset="utf-8">
<title>Brightmoor Nutrition – Supplement Labels</title>
<link rel="stylesheet" href="https://fonts.googleapis.com/css2?family=Oswald:wght@400;500;600&family=Russo+One&family=Roboto:wght@400;700&display=swap">
<style>
  :root {
    --page: #ffffff;
    --ink: #111111;
    --label-black: #0b0b0b;
    --label-dark: #1a1a1a;
    --green: #3ef12e;
    --green-deep: #1f9e16;
    --red: #e3262e;
    --red-deep: #8c1217;
    --white: #ffffff;
    --muted: #bdbdbd;
    --rule: #c9c9c9;
  }
  * { box-sizing: border-box; margin: 0; padding: 0; }
  html, body { width: 1200px; height: 2400px; overflow: hidden; background: var(--page); }
  body { position: relative; font-family: "Roboto", Arial, sans-serif; color: var(--ink); }

  .brand-header { position: absolute; top: 120px; left: 0; width: 1200px; text-align: center; }
  .brand-header__mark { display: inline-block; width: 22px; height: 22px; background: var(--red); vertical-align: middle; margin-right: 14px; }
  .brand-header__name { display: inline-block; vertical-align: middle; font-family: "Oswald", sans-serif; font-weight: 500; font-size: 32px; letter-spacing: 3px; color: var(--ink); }
  .brand-header__rule { position: absolute; top: 245px; left: 596px; width: 534px; height: 1px; background: var(--rule); }

  .label { position: absolute; left: 100px; width: 1000px; overflow: hidden; color: var(--white); }
  .label--greens { top: 720px; height: 378px; background: radial-gradient(ellipse at 50% 50%, #202020 0%, #0d0d0d 60%, #050505 100%); }
  .label--preworkout { top: 1640px; height: 222px; background: radial-gradient(ellipse at 50% 50%, #1e1e1e 0%, #0c0c0c 60%, #050505 100%); }

  .label__texture { position: absolute; inset: 0; background: linear-gradient(135deg, rgba(255,255,255,0.03), rgba(255,255,255,0) 50%, rgba(255,255,255,0.03)); }
  .label__lines { position: absolute; inset: 0; }

  .label__brand { position: absolute; left: 0; width: 100%; text-align: center; font-family: "Oswald", sans-serif; font-weight: 500; letter-spacing: 1.5px; }
  .label__brand-mark { display: block; margin: 0 auto 6px; background: var(--red); }
  .label__title { position: absolute; left: 0; width: 100%; text-align: center; font-family: "Russo One", sans-serif; font-style: italic; transform: skewX(-8deg); color: var(--white); letter-spacing: 1px; }
  .label__flavor { position: absolute; left: 50%; transform: translateX(-50%) skewX(-18deg); font-family: "Oswald", sans-serif; font-weight: 500; text-align: center; letter-spacing: 1px; }

  .benefits { position: absolute; left: 0; width: 100%; display: flex; justify-content: center; }
  .benefit { text-align: center; font-size: 7.5px; line-height: 1.2; letter-spacing: .5px; text-transform: uppercase; }
  .benefit svg { display: block; margin: 0 auto 4px; }

  .label__footer { position: absolute; font-weight: 700; }

  .panel-box { position: absolute; border-radius: 6px; font-size: 7.5px; line-height: 1.3; color: var(--white); background: rgba(0,0,0,0.55); }
  .panel-box strong { font-weight: 700; }
  .label--greens .panel-box { border: 1px solid var(--green-deep); padding: 8px 9px; }
  .label--preworkout .panel-box { border: 1px solid #9a9a9a; padding: 6px 8px; }
  .panel-box--note { font-size: 4.6px; line-height: 1.25; text-align: center; }

  .facts { position: absolute; background: var(--white); color: var(--ink); font-size: 4.6px; line-height: 1.35; padding: 5px 6px; }
  .facts__title { font-weight: 700; font-size: 9px; border-bottom: 1px solid var(--ink); padding-bottom: 2px; margin-bottom: 2px; }
  .facts__row { display: flex; justify-content: space-between; border-bottom: .5px solid #cccccc; }
  .facts__row span:nth-child(2) { margin-left: auto; width: 40px; text-align: right; }
  .facts__row span:nth-child(3) { width: 22px; text-align: right; }
  .facts__head { font-weight: 700; border-bottom: 1.5px solid var(--ink); }
  .facts__blend { font-weight: 700; }
  .facts__note { margin-top: 3px; }
  .ingredients { position: absolute; font-size: 4.6px; line-height: 1.3; color: var(--white); }
</style>
</head>
<body>

<header class="brand-header">
  <span class="brand-header__mark"></span><span class="brand-header__name">BRIGHTMOOR NUTRITION</span>
</header>
<div class="brand-header__rule"></div>

<!-- Super Green wrap label -->
<section class="label label--greens">
  <div class="label__texture" role="img" aria-label="Dark hexagon texture"></div>
  <svg class="label__lines" width="1000" height="378" viewBox="0 0 1000 378">
    <defs>
      <filter id="glowGreen" x="-50%" y="-50%" width="200%" height="200%"><feGaussianBlur stdDeviation="3" result="b"/><feMerge><feMergeNode in="b"/><feMergeNode in="SourceGraphic"/></feMerge></filter>
    </defs>
    <g stroke="#3ef12e" stroke-width="2.5" fill="none" filter="url(#glowGreen)">
      <polyline points="170,0 300,189 170,378"/>
      <polyline points="230,60 320,189 230,318" stroke-width="1.5" opacity=".7"/>
      <polyline points="830,0 700,189 830,378"/>
      <polyline points="770,60 680,189 770,318" stroke-width="1.5" opacity=".7"/>
      <line x1="200" y1="189" x2="300" y2="189" stroke-width="1" opacity=".6"/>
      <line x1="700" y1="189" x2="1000" y2="189" stroke-width="1" opacity=".6"/>
    </g>
  </svg>

  <div class="panel-box" style="left:20px;top:40px;width:118px;">
    <strong>Directions:</strong> Mix one (1) scoop into 6-8oz of your favorite non-citrus juice, water, smoothie, or protein shake.
  </div>
  <div class="panel-box" style="left:20px;top:118px;width:118px;">
    <strong>CAUTION:</strong> As with any dietary supplement, consult your healthcare practitioner before using this product, especially if you are pregnant, nursing, anticipate surgery, take medication on a regular basis or otherwise under medical supervision. Store in a cool, dry place. Keep out of reach of children.
  </div>
  <div class="panel-box panel-box--note" style="left:20px;top:262px;width:118px;color:var(--green);padding:4px;">
    *These statements have not been evaluated by the Food and Drug Administration. This product is not intended to diagnose, treat, cure or prevent any disease.
  </div>

  <div class="label__brand" style="top:24px;font-size:15px;">
    <span class="label__brand-mark" style="width:16px;height:16px;"></span>BRIGHTMOOR NUTRITION
  </div>
  <div class="label__title" style="top:96px;font-size:50px;">SUPER GREEN</div>
  <div class="label__flavor" style="top:168px;width:150px;padding:3px 0;background:var(--green);color:var(--ink);font-size:13px;">APPLE CINNAMON</div>

  <div class="benefits" style="top:222px;gap:50px;">
    <div class="benefit" style="width:50px;">
      <svg width="34" height="22" viewBox="0 0 34 22"><path d="M17 11 C12 3 3 3 3 11 C3 19 12 19 17 11 C22 3 31 3 31 11 C31 19 22 19 17 11 Z" fill="none" stroke="#3ef12e" stroke-width="4"/></svg>
      DETOX<br>BODY *
    </div>
    <div class="benefit" style="width:80px;">
      <svg width="24" height="34" viewBox="0 0 24 34"><path d="M12 1 V6 H5 C2 6 2 11 5 11 H19 C22 11 22 16 19 16 H5 C2 16 2 21 5 21 H19 C22 21 22 26 19 26 H12 V33" fill="none" stroke="#3ef12e" stroke-width="3" stroke-linecap="round" stroke-linejoin="round"/></svg>
      PROMOTE HEALTHY<br>DIGESTION *
    </div>
    <div class="benefit" style="width:60px;">
      <svg width="28" height="32" viewBox="0 0 28 32"><path d="M14 1 L26 6 V15 C26 23 20 28 14 31 C8 28 2 23 2 15 V6 Z" fill="#3ef12e"/><path d="M14 10 V22 M8 16 H20" stroke="#0b0b0b" stroke-width="3.5"/></svg>
      SUPPORT<br>IMMUNITY *
    </div>
  </div>

  <div class="label__footer" style="left:305px;top:334px;font-size:10px;">Dietary Supplement</div>
  <div class="label__footer" style="right:310px;top:334px;font-size:10px;">30 Servings &nbsp;270g (9.5oz)</div>

  <div class="facts" style="left:722px;top:42px;width:262px;">
    <div class="facts__title">Supplement Facts</div>
    <div>Serving Size: Approx. 1 Scoop (9 g)</div>
    <div>Servings per Container: 30</div>
    <div class="facts__row facts__head"><span></span><span>Amount per Serving</span><span>%DV</span></div>
    <div class="facts__row"><span>Calories</span><span>40</span><span></span></div>
    <div class="facts__row"><span>Total Carbohydrate</span><span>1.5 g</span><span>2%</span></div>
    <div class="facts__row"><span>&nbsp;&nbsp;Dietary Fiber</span><span>1 g</span><span>3%</span></div>
    <div class="facts__row"><span>&nbsp;&nbsp;Total Sugars</span><span>1 g</span><span>†</span></div>
    <div class="facts__row"><span>Vitamin E (as d-Alpha Tocopherol)</span><span>2.5 mg</span><span>17%</span></div>
    <div class="facts__row"><span>Potassium</span><span>110 mg</span><span>2%</span></div>
    <div class="facts__row facts__blend"><span>Green Health Blend</span><span>5.6 g</span><span>†</span></div>
    <div>Soy Lecithin, Apple Fruit, Barley Grass, Wheat Grass, Alfalfa, Spinach, Spirulina, Chlorella, Broccoli</div>
    <div class="facts__row facts__blend"><span>Energy Blend</span><span>1.6 g</span><span>†</span></div>
    <div>Acerola Cherry, Beet Root, Bee Pollen, Green Tea Leaf Extract</div>
    <div class="facts__row facts__blend"><span>Detox Blend</span><span>620 mg</span><span>†</span></div>
    <div>Milk Thistle Seed, Dandelion Root, Parsley Leaf, Ginger Root</div>
    <div class="facts__row facts__blend"><span>Probiotic Blend Complex</span><span>180 mg</span><span>†</span></div>
    <div>Lactobacillus acidophilus, Bifidobacterium bifidum, Lactobacillus rhamnosus</div>
    <div class="facts__row facts__blend"><span>Enzyme Blend</span><span>120 mg</span><span>†</span></div>
    <div>Amylase, Bromelain, Papain, Cellulase, Lipase, Protease</div>
    <div class="facts__note">† Daily Value not established. Percent Daily Values are based on a 2,000 calorie diet.</div>
    <div class="facts__note"><strong>Other Ingredients:</strong> Natural Apple Cinnamon Flavor, Citric Acid, Stevia Leaf Extract, Silicon Dioxide.</div>
    <div class="facts__note"><strong>Formulated by:</strong> Club Brightmoor</div>
  </div>
</section>

<!-- Pre-Workout wrap label -->
<section class="label label--preworkout">
  <div class="label__texture" role="img" aria-label="Dark hexagon texture"></div>
  <svg class="label__lines" width="1000" height="222" viewBox="0 0 1000 222">
    <defs>
      <filter id="glowRed" x="-50%" y="-50%" width="200%" height="200%"><feGaussianBlur stdDeviation="3" result="b"/><feMerge><feMergeNode in="b"/><feMergeNode in="SourceGraphic"/></feMerge></filter>
    </defs>
    <g stroke="#e3262e" stroke-width="2.5" fill="none" filter="url(#glowRed)">
      <polyline points="210,0 310,111 210,222"/>
      <polyline points="255,35 330,111 255,187" stroke-width="1.5" opacity=".7"/>
      <polyline points="790,0 690,111 790,222"/>
      <polyline points="745,35 670,111 745,187" stroke-width="1.5" opacity=".7"/>
    </g>
  </svg>

  <div class="panel-box" style="left:22px;top:18px;width:236px;font-size:4.8px;line-height:1.3;">
    <strong>Directions:</strong> Use on training days only. Mix 1 scoop with 8-10 oz of cold water 15-30 minutes prior to training.<br>
    <strong>Warning:</strong> Not intended for use by persons under age 18. Do not exceed recommended dose. Do not combine with caffeine from other sources, including coffee, tea, soda and other dietary supplements. Contains caffeine. Consult your physician before use if you are pregnant, nursing or taking any medication, or if you have a known medical condition including heart, liver, kidney or thyroid disease, high blood pressure or diabetes. Discontinue use two weeks prior to surgery or if you experience rapid heartbeat, dizziness, severe headache or shortness of breath. Keep out of reach of children.
  </div>
  <div class="panel-box panel-box--note" style="left:22px;top:172px;width:92px;padding:3px;border-radius:8px;">
    *These statements have not been evaluated by the Food and Drug Administration. This product is not intended to diagnose, treat, cure or prevent any disease.
  </div>

  <div class="label__brand" style="top:14px;font-size:8.5px;">
    <span class="label__brand-mark" style="width:10px;height:10px;margin-bottom:4px;"></span>BRIGHTMOOR NUTRITION
  </div>
  <div class="label__title" style="top:50px;font-size:33px;">PRE-WORKOUT</div>
  <div class="label__flavor" style="top:93px;width:120px;color:var(--red);font-size:10px;">WATERMELON SUGAR</div>

  <div class="benefits" style="top:126px;gap:36px;">
    <div class="benefit" style="width:50px;font-size:6.5px;">
      <svg width="16" height="16" viewBox="0 0 16 16"><rect x="1" y="1" width="14" height="14" rx="2" fill="none" stroke="#e3262e" stroke-width="1.3"/><path d="M9 3 L5 9 H8 L7 13 L11 7 H8 Z" fill="#e3262e"/></svg>
      <strong>ENERGY*</strong><br><span style="color:var(--muted);">CAFFEINE</span>
    </div>
    <div class="benefit" style="width:70px;font-size:6.5px;">
      <svg width="16" height="16" viewBox="0 0 16 16"><rect x="1" y="1" width="14" height="14" rx="2" fill="none" stroke="#e3262e" stroke-width="1.3"/><path d="M8 3 L12 8 H9.5 V13 H6.5 V8 H4 Z" fill="#e3262e"/></svg>
      <strong>PERFORMANCE*</strong><br><span style="color:var(--muted);">BETA-ALANINE</span>
    </div>
    <div class="benefit" style="width:50px;font-size:6.5px;">
      <svg width="16" height="16" viewBox="0 0 16 16"><rect x="1" y="1" width="14" height="14" rx="2" fill="none" stroke="#e3262e" stroke-width="1.3"/><path d="M4 5 V11 M12 5 V11 M5.5 6.5 V9.5 M10.5 6.5 V9.5 M5.5 8 H10.5" stroke="#e3262e" stroke-width="1.4"/></svg>
      <strong>STRENGTH*</strong><br><span style="color:var(--muted);">CREATINE</span>
    </div>
  </div>

  <div class="label__footer" style="left:315px;top:200px;font-family:'Oswald',sans-serif;font-weight:500;font-size:6.5px;letter-spacing:.5px;">DIETARY SUPPLEMENT</div>
  <div class="label__footer" style="right:318px;top:200px;font-family:'Oswald',sans-serif;font-weight:500;font-size:6.5px;letter-spacing:.5px;">30 SERVINGS 240g (8.5oz)</div>

  <div class="facts" style="left:798px;top:16px;width:184px;font-size:4.4px;">
    <div class="facts__title" style="font-size:7px;">Supplement Facts</div>
    <div class="facts__row facts__head"><span></span><span>Amount per Serving</span><span>%DV</span></div>
    <div class="facts__row"><span>Vitamin B6 (as Pyridoxal-5-Phosphate)</span><span>35 mg</span><span>2059%</span></div>
    <div class="facts__row"><span>Vitamin B12 (as Methylcobalamin)</span><span>500 mcg</span><span>20833%</span></div>
    <div class="facts__row"><span>Beta-Alanine</span><span>2 g</span><span>†</span></div>
    <div class="facts__row"><span>Creatine Monohydrate</span><span>1.5 g</span><span>†</span></div>
    <div class="facts__row"><span>L-Citrulline</span><span>1 g</span><span>†</span></div>
    <div class="facts__row"><span>L-Arginine Alpha-Ketoglutarate</span><span>1 g</span><span>†</span></div>
    <div class="facts__row"><span>Betaine Anhydrous</span><span>500 mg</span><span>†</span></div>
    <div class="facts__row"><span>Caffeine Anhydrous</span><span>200 mg</span><span>†</span></div>
    <div class="facts__row"><span>L-Tyrosine</span><span>50 mg</span><span>†</span></div>
    <div class="facts__note">† Daily Value (DV) not established</div>
  </div>
  <div class="ingredients" style="left:798px;top:166px;width:184px;">
    <strong>Other Ingredients:</strong> Citric Acid, Natural and Artificial Flavors, Silicon Dioxide, Sucralose, Beet Root Color.<br><br>
    <strong>Formulated by:</strong> Club Brightmoor
  </div>
</section>

</body>
</html>
```